TALMORK

The business want a professional looking business card. We have a scetch we will add but want the extra upgrade, and would like more suggestions for variations of our business cards.

```html
<!DOCTYPE html>
<html lang="en">
<head>
<meta charset="UTF-8">
<title>TALMORK Business Card</title>
<link rel="stylesheet" href="https://fonts.googleapis.com/css2?family=Cinzel:wght@400;600;700&family=Montserrat:wght@400;500&display=swap">
<style>
  :root {
    --backdrop: #e3e3e3;
    --paper: #f8f8f6;
    --brown: #6b4a1c;
    --gold-light: #e6dcbd;
    --gold-mid: #c7a862;
    --gold-deep: #7c5a27;
    --gold-dark: #5b4019;
    --ink-light: #ffffff;
  }
  * { box-sizing: border-box; margin: 0; padding: 0; }
  html, body { width: 1200px; height: 900px; overflow: hidden; }
  body {
    background: var(--backdrop);
    position: relative;
    font-family: "Montserrat", sans-serif;
  }
  .card {
    position: absolute;
    width: 600px;
    height: 343px;
    border-radius: 22px;
    box-shadow: 0 10px 24px rgba(0,0,0,0.18);
    overflow: hidden;
  }
  .card--front {
    left: 110px;
    top: 80px;
    background: var(--paper);
  }
  .card--back {
    left: 490px;
    top: 475px;
    background: linear-gradient(60deg, var(--gold-light) 0%, var(--gold-mid) 32%, var(--gold-deep) 68%, var(--gold-dark) 100%);
    color: var(--ink-light);
  }
  .wordmark {
    font-family: "Cinzel", serif;
    font-weight: 600;
    letter-spacing: 0.14em;
    line-height: 1;
  }
  .tagline {
    font-family: "Montserrat", sans-serif;
    letter-spacing: 0.42em;
    line-height: 1;
  }
  .front-lockup {
    position: absolute;
    left: 0; right: 0; top: 132px;
    text-align: center;
    color: var(--brown);
    padding-left: 60px;
  }
  .front-lockup .wordmark { font-size: 52px; }
  .front-lockup .tagline { font-size: 14px; margin-top: 12px; padding-left: 70px; }
  .back-lockup {
    position: absolute;
    left: 42px;
    top: 118px;
    width: 230px;
    text-align: center;
  }
  .brand-dot {
    display: block;
    width: 64px; height: 64px;
    border-radius: 50%;
    background: var(--ink-light);
    margin: 0 auto 18px;
  }
  .back-lockup .wordmark { font-size: 30px; }
  .back-lockup .tagline { font-size: 9px; margin-top: 8px; }
  .details {
    position: absolute;
    left: 318px;
    top: 62px;
    width: 270px;
  }
  .person-name {
    font-family: "Cinzel", serif;
    font-weight: 700;
    font-size: 17px;
    letter-spacing: 0.02em;
  }
  .role {
    font-size: 19px;
    font-weight: 400;
    margin-top: 4px;
  }
  .person-sub {
    font-size: 9.5px;
    opacity: 0.85;
    margin-top: 3px;
  }
  .contacts { list-style: none; margin-top: 52px; }
  .contacts li {
    display: flex;
    align-items: center;
    gap: 8px;
    font-size: 12.5px;
    margin-bottom: 9px;
  }
  .contacts svg { width: 13px; height: 13px; flex: none; fill: var(--ink-light); }
</style>
</head>
<body>
  <section class="card card--front" aria-label="Card front">
    <div class="front-lockup">
      <div class="wordmark">TALMORK</div>
      <div class="tagline">SINCE 2026</div>
    </div>
  </section>

  <section class="card card--back" aria-label="Card back">
    <div class="back-lockup">
      <span class="brand-dot"></span>
      <div class="wordmark">TALMORK</div>
      <div class="tagline">SINCE 2026</div>
    </div>
    <div class="details">
      <h1 class="person-name">TALMORK BREKKESTAD</h1>
      <p class="role">CEO &amp; Founder</p>
      <p class="person-sub">Lars Ove Brekkestad</p>
      <ul class="contacts">
        <li>
          <svg viewBox="0 0 24 24" aria-hidden="true"><path d="M6.6 10.8a15 15 0 0 0 6.6 6.6l2.2-2.2a1 1 0 0 1 1-.25 11.4 11.4 0 0 0 3.6.57 1 1 0 0 1 1 1V20a1 1 0 0 1-1 1A17 17 0 0 1 3 4a1 1 0 0 1 1-1h3.5a1 1 0 0 1 1 1c0 1.25.2 2.45.57 3.6a1 1 0 0 1-.25 1z"/></svg>
          004791234567
        </li>
        <li>
          <svg viewBox="0 0 24 24" aria-hidden="true"><path d="M3 5h18a1 1 0 0 1 1 1v12a1 1 0 0 1-1 1H3a1 1 0 0 1-1-1V6a1 1 0 0 1 1-1zm9 7.5L20 7H4z"/></svg>
          talmork.llc@mailbox.com
        </li>
        <li>
          <svg viewBox="0 0 24 24" aria-hidden="true"><circle cx="12" cy="12" r="10"/></svg>
          www.talmork.llc
        </li>
      </ul>
    </div>
  </section>
</body>
</html>
```